Investment company needing business card

We are wanting a business card which looks sharp and easy on the eye. We are thinking of having a business card with the logo embossed on it, to really make it stand out. We will only have a small amount of information of the business card, person's name, position, email address and phone number

Contact Information for Business Card

Danielle Frost
Executive Assistant
+64 21 473 5162
danielf@harwickpartners.co.nz

Requirements
Must have
• Embossed logo
Should not have
• Not to be busy

```html
<!DOCTYPE html>
<html lang="en">
<head>
<meta charset="utf-8">
<title>Harwick Partners – Business Card</title>
<link href="https://fonts.googleapis.com/css2?family=Open+Sans:wght@400;600;700&display=swap" rel="stylesheet">
<style>
  :root {
    --brand-green: #23b574;
    --band-grey: #a9a9a9;
    --ink: #4f4f4f;
    --paper: #ffffff;
    --backdrop: #e9e6e3;
  }
  html, body {
    margin: 0;
    width: 1200px;
    height: 997px;
    overflow: hidden;
    background: var(--backdrop);
    font-family: "Open Sans", Arial, sans-serif;
  }
  .stage { position: relative; width: 1200px; height: 997px; }
  .card {
    position: absolute;
    left: 250px;
    width: 700px;
    height: 400px;
    overflow: hidden;
    box-shadow: 0 6px 18px rgba(0,0,0,0.12);
  }
  .card-front { top: 70px; background: var(--paper); }
  .card-back { top: 527px; background: var(--brand-green); }
  .front-art { position: absolute; inset: 0; }
  .wordmark {
    position: absolute;
    display: flex;
    align-items: center;
    gap: 12px;
    font-weight: 700;
    letter-spacing: 1px;
  }
  .wordmark-square { width: 40px; height: 40px; }
  .wordmark-text { line-height: 1.05; }
  .wordmark-name { display: block; font-size: 34px; }
  .wordmark-sub { display: block; font-size: 14px; letter-spacing: 6px; }
  .card-front .wordmark { left: 40px; top: 130px; color: var(--brand-green); }
  .card-front .wordmark-square { background: var(--brand-green); }
  .card-back .wordmark { left: 50%; top: 50%; transform: translate(-50%, -50%); color: var(--paper); }
  .card-back .wordmark-square { background: var(--paper); }
  .person-name {
    position: absolute; left: 365px; top: 101px;
    color: var(--paper); font-weight: 700; font-size: 19px;
  }
  .person-role {
    position: absolute; left: 470px; top: 133px;
    color: var(--paper); font-size: 15px;
  }
  .contact-list {
    position: absolute; left: 40px; bottom: 34px;
    margin: 0; padding: 0; list-style: none;
    color: var(--ink); font-size: 16px; line-height: 24px;
  }
  .contact-list li { display: flex; align-items: center; gap: 8px; }
  .contact-icon { width: 12px; height: 12px; fill: var(--brand-green); }
</style>
</head>
<body>
<main class="stage">
  <section class="card card-front">
    <svg class="front-art" width="700" height="400" viewBox="0 0 700 400" aria-hidden="true">
      <polygon points="300,0 700,0 700,215" fill="var(--brand-green)"/>
      <polygon points="445,72 700,72 700,100 430,100" fill="var(--band-grey)"/>
      <polygon points="355,100 640,100 640,130 340,130" fill="var(--brand-green)"/>
      <polygon points="440,130 700,130 700,158 425,158" fill="var(--band-grey)"/>
    </svg>
    <div class="wordmark">
      <span class="wordmark-square"></span>
      <span class="wordmark-text"><span class="wordmark-name">HARWICK</span><span class="wordmark-sub">PARTNERS</span></span>
    </div>
    <div class="person-name">Danielle Frost</div>
    <div class="person-role">Executive Assistant</div>
    <ul class="contact-list">
      <li><svg class="contact-icon" viewBox="0 0 12 12"><path d="M2 1l2 0 1 3-1.5 1a6 6 0 0 0 3.5 3.5L8 7l3 1v2a1 1 0 0 1-1 1A9 9 0 0 1 1 2a1 1 0 0 1 1-1z"/></svg>+64 21 473 5162</li>
      <li><svg class="contact-icon" viewBox="0 0 12 12"><path d="M0 2h12v8H0z M0 2l6 4 6-4" stroke="#fff" stroke-width="1"/></svg>danielf@harwickpartners.co.nz</li>
      <li><svg class="contact-icon" viewBox="0 0 12 12"><circle cx="6" cy="6" r="6"/></svg>www.harwickpartners.co.nz</li>
    </ul>
  </section>
  <section class="card card-back">
    <div class="wordmark">
      <span class="wordmark-square"></span>
      <span class="wordmark-text"><span class="wordmark-name">HARWICK</span><span class="wordmark-sub">PARTNERS</span></span>
    </div>
  </section>
</main>
</body>
</html>
```